Creative, fresh business card design for Ripplecraft Facades

We need a fresh, creative business card design for Ripplecraft Facades. We are the manufacturer of Ripplecraft Facades in Australia. Wall panels are 2400 x 1200mm panels made from MDF and feature 3D patterns on the face of the panel. The colours to be used are green, silver/grey and white RGB
Red 187
Green 207
Blue 65.

An idea is to possibly use a watermark of one of our designs as a background (like on the "Grids" design on the left hand side of page 2 of our brochure).

Target Market(s)

Interior designers, architects, builders and home renovators

Industry/Entity Type

Business

Contact Information for Business Card

Details to go on the card are:
Our logo (attached),
Slogan: "Decorative panels for interiors and exteriors",
Daniel Harker,
Position,
Mobile phone number,
Business address,
Business phone,
Business fax,
Website and
Email address.

I have attached a few images of our panels and our brochure for reference.

The colours of the business card should feature our logo colours which are: RGB
Red 187
Green 207
Blue 65

Requirements
Must have
• Very modern fonts and design. Some of the designs shown especially the "Prisms" design which is a popular design.
Nice to have
• Creative but simple design. Very contemporary.
Should not have
• Anything ornate or old fashioned.

```html
<!DOCTYPE html>
<html lang="en">
<head>
<meta charset="utf-8">
<title>Ripplecraft Facades – Business Card</title>
<link rel="stylesheet" href="https://fonts.googleapis.com/css2?family=Carlito:wght@400;700&family=Marcellus&display=swap">
<style>
  :root {
    --backdrop: #333136;
    --brand-green: rgb(187, 207, 65);
    --brand-grey: #808083;
    --card-white: #f4f3f0;
    --card-shade: #e2e0dc;
    --ink: #3a3a3a;
    --ink-soft: #4a4a4a;
  }
  * { margin: 0; padding: 0; box-sizing: border-box; }
  html, body {
    width: 1200px;
    height: 1000px;
    overflow: hidden;
    background: var(--backdrop);
  }
  .canvas {
    position: relative;
    width: 1200px;
    height: 1000px;
  }

  /* Brand name block shown above the card */
  .brand-header {
    position: absolute;
    top: 36px;
    left: 367px;
    width: 420px;
    height: 143px;
    display: flex;
    align-items: center;
    justify-content: center;
    gap: 18px;
  }
  .brand-header .brand-square {
    width: 34px;
    height: 34px;
    background: var(--brand-green);
    flex: none;
  }
  .brand-header .brand-name {
    font-family: "Carlito", sans-serif;
    font-size: 40px;
    color: #d6d6d8;
    letter-spacing: 0.5px;
    white-space: nowrap;
  }

  /* Business card front */
  .business-card {
    position: absolute;
    top: 258px;
    left: 205px;
    width: 647px;
    height: 362px;
    overflow: hidden;
    box-shadow: 0 4px 14px rgba(0, 0, 0, 0.45);
  }
  .card-texture {
    position: absolute;
    inset: 0;
    background:
      linear-gradient(180deg, var(--card-white) 0%, var(--card-shade) 20%, var(--card-white) 38%, var(--card-shade) 58%, var(--card-white) 76%, var(--card-shade) 100%);
  }
  .card-content {
    position: absolute;
    left: 352px;
    top: 55px;
    width: 290px;
  }
  .card-brand {
    display: flex;
    align-items: center;
    gap: 10px;
    height: 108px;
  }
  .card-brand .brand-square {
    width: 20px;
    height: 20px;
    background: var(--brand-green);
    flex: none;
  }
  .card-brand .brand-name {
    font-family: "Carlito", sans-serif;
    font-size: 23px;
    color: var(--ink-soft);
    white-space: nowrap;
  }
  .tagline {
    font-family: "Marcellus", serif;
    font-size: 16px;
    line-height: 19px;
    color: var(--ink);
    margin-top: 11px;
  }
  .contact-list {
    list-style: none;
    margin-top: 33px;
    font-family: "Carlito", sans-serif;
    font-size: 14px;
    line-height: 20.5px;
    color: var(--ink);
    white-space: nowrap;
  }

  /* Personal details, lower left of the card */
  .card-person {
    position: absolute;
    left: 34px;
    bottom: 28px;
    font-family: "Carlito", sans-serif;
    color: var(--ink);
    white-space: nowrap;
  }
  .card-person .person-name {
    font-size: 18px;
    font-weight: 700;
    line-height: 22px;
  }
  .card-person .person-role {
    font-size: 14px;
    line-height: 20.5px;
    color: var(--brand-grey);
  }
  .card-person .person-mobile {
    font-size: 14px;
    line-height: 20.5px;
  }
</style>
</head>
<body>
<main class="canvas">
  <header class="brand-header">
    <span class="brand-square"></span>
    <span class="brand-name">Ripplecraft Facades</span>
  </header>

  <section class="business-card">
    <div class="card-texture" role="img" aria-label="White sculpted wall panel with flowing horizontal wave relief"></div>

    <div class="card-person">
      <p class="person-name">Daniel Harker</p>
      <p class="person-role">Sales Manager</p>
      <p class="person-mobile">Mobile: 0400 555 318</p>
    </div>

    <div class="card-content">
      <div class="card-brand">
        <span class="brand-square"></span>
        <span class="brand-name">Ripplecraft Facades</span>
      </div>
      <p class="tagline">decorative panels for<br>interiors &amp; exteriors</p>
      <ul class="contact-list">
        <li>Telephone: 02 5550 1842</li>
        <li>Business fax: 02 5550 1843</li>
        <li>14 Kestrel Lane, Marrowvale NSW 2190</li>
        <li>www.ripplecraftfacades.com.au</li>
        <li>sales@ripplecraftfacades.com.au</li>
      </ul>
    </div>
  </section>
</main>
</body>
</html>
```